Business Card Design - VNT (company name)

Over 20 years of progressive technology design, migration and management experience that drives business objectives and streamlines operations. Continuously challenge conventions to meet and exceed business security, availability and functionality requirements. Maintain exceptional vendor relationships to ensure ongoing knowledge of emerging products and to secure preferred service agreements. Recruit and utilize top talent and foster a collegial environment that advances innovation and performance excellence. design logo using 3 arrows of different colors green, gold, blue

Industry/Entity Type

Progressive

Contact Information for Business Card

Martin K. Osgood
IT Strategist / Consultant

626.583.2907 MOsgood@vntosgood.example 4817 Brenning Court Pasadena, CA 91104

Colors
0255a3
f37122
fece3e

Requirements
Must have
• Note NEW EMAIL ADDRESS
• MOsgood@vntosgood.example
• NOTE NEW ORDER of the work I do.
• Infrastructure – Systems – Cybersecurity
Nice to have
• main color should be orange

```html
<!DOCTYPE html>
<html lang="en">
<head>
<meta charset="utf-8">
<title>VNT Business Card</title>
<link rel="stylesheet" href="https://fonts.googleapis.com/css2?family=Open+Sans:wght@400;600;700&display=swap">
<style>
  :root {
    --backdrop: #8f8f8d;
    --card: #0b0b0b;
    --card-edge: #161616;
    --text-light: #f2f2f2;
    --brand-blue: #0255a3;
    --brand-orange: #f37122;
    --brand-gold: #fece3e;
    --icon-blue: #1f6fc4;
  }
  * { margin: 0; padding: 0; box-sizing: border-box; }
  html, body {
    width: 1200px;
    height: 900px;
    overflow: hidden;
    background: var(--backdrop);
    font-family: "Open Sans", "Segoe UI", sans-serif;
  }
  .canvas {
    position: relative;
    width: 1200px;
    height: 900px;
  }
  .card {
    position: absolute;
    left: 290px;
    width: 620px;
    height: 354px;
    background: radial-gradient(ellipse at 45% 35%, var(--card-edge), var(--card) 70%);
    color: var(--text-light);
    box-shadow: 0 6px 18px rgba(0, 0, 0, 0.25);
  }
  .card--back { top: 70px; }
  .card--front { top: 476px; }

  /* Back of card */
  .services {
    position: absolute;
    right: 338px;
    top: 104px;
    text-align: right;
    font-size: 17px;
    line-height: 23px;
    font-weight: 400;
    list-style: none;
    white-space: nowrap;
  }
  .brand-mark {
    position: absolute;
    display: flex;
    align-items: center;
    gap: 12px;
    color: var(--brand-orange);
    font-weight: 700;
    letter-spacing: 2px;
    white-space: nowrap;
  }
  .brand-mark__dot {
    width: 18px;
    height: 18px;
    border-radius: 50%;
    background: var(--brand-orange);
  }
  .card--back .brand-mark {
    left: 320px;
    top: 118px;
    font-size: 62px;
    line-height: 1;
  }

  /* Front of card */
  .card--front .brand-mark {
    left: 50%;
    transform: translateX(-50%);
    top: 44px;
    font-size: 54px;
    line-height: 1;
  }
  .identity {
    position: absolute;
    left: 0;
    right: 0;
    top: 136px;
    text-align: center;
  }
  .identity__name {
    font-size: 25px;
    font-weight: 600;
    line-height: 30px;
  }
  .identity__role {
    font-size: 17px;
    color: var(--brand-blue);
    line-height: 22px;
  }
  .address {
    position: absolute;
    left: 34px;
    top: 214px;
    font-size: 17px;
    line-height: 22px;
    font-style: normal;
  }
  .contact {
    position: absolute;
    right: 34px;
    bottom: 36px;
    list-style: none;
    font-size: 17px;
    line-height: 28px;
    text-align: right;
  }
  .contact__item {
    display: flex;
    align-items: center;
    justify-content: flex-end;
    gap: 10px;
  }
  .contact__icon {
    width: 20px;
    height: 20px;
    display: block;
  }
</style>
</head>
<body>
<main class="canvas">

  <section class="card card--back" aria-label="Business card back">
    <ul class="services">
      <li>IT Strategist / Consultant</li>
      <li>Infrastructure</li>
      <li>Systems</li>
      <li>Cybersecurity</li>
    </ul>
    <div class="brand-mark"><span class="brand-mark__dot"></span>VNT</div>
  </section>

  <section class="card card--front" aria-label="Business card front">
    <div class="brand-mark"><span class="brand-mark__dot"></span>VNT</div>
    <div class="identity">
      <p class="identity__name">John Smith</p>
      <p class="identity__role">Managing Director</p>
    </div>
    <address class="address">
      12345, Address Goes Here<br>
      Country Name, 123456
    </address>
    <ul class="contact">
      <li class="contact__item">
        <span>123-456-7890</span>
        <svg class="contact__icon" viewBox="0 0 20 20" aria-hidden="true">
          <rect width="20" height="20" rx="3" fill="var(--icon-blue)"/>
          <rect x="6.5" y="3.5" width="7" height="13" rx="1.2" fill="none" stroke="#fff" stroke-width="1.4"/>
          <circle cx="10" cy="14" r="0.9" fill="#fff"/>
        </svg>
      </li>
      <li class="contact__item">
        <span>info@youremail.com</span>
        <svg class="contact__icon" viewBox="0 0 20 20" aria-hidden="true">
          <rect width="20" height="20" rx="3" fill="var(--icon-blue)"/>
          <rect x="4" y="6" width="12" height="8.5" fill="#fff"/>
          <path d="M4 6 L10 11 L16 6" fill="none" stroke="var(--icon-blue)" stroke-width="1.3"/>
        </svg>
      </li>
    </ul>
  </section>

</main>
</body>
</html>
```